Creative Alcoholic Beverage Package Design Needed!

We need a packaging design for a new alcoholic beverage, including the brand name. Flavours will include Sangria and Margarita, and future line extensions as well. Package will be a box (see attached dieline and example of a competitive product) in a 3 liter format. The dimensions of the box need to match the dieline, but we can be creative on the printing of the box. The product inside will be of high-quality, so the design needs to match this
Updates

Need extra days to review

Target Market(s)

25 to 40 year old, 70% female, 30% male

Colors

Designer to choose colors to be used in the design.

Requirements
Must have
• Be attractive, colourful, modern
• clearly mention the flavour, and show the components of the flavour (Sangria : red wine and citrus) - Margarita (mexican inspiration, lime, etc.)
• Have a clear "brand name" along with the flavours
• Mention the quantity (3 liters), alcohol level : 10% alc./vol.

```html
<!DOCTYPE html>
<html lang="en">
<head>
<meta charset="utf-8">
<title>Corvella Sangria – 3 L Box</title>
<link rel="stylesheet" href="https://fonts.googleapis.com/css2?family=Della+Respira&family=Almendra:wght@700&family=Crimson+Text:wght@400;700&display=swap">
<style>
  :root {
    --backdrop: #ececec;
    --maroon-deep: #1c0306;
    --maroon: #3a070d;
    --wine: #6e0f18;
    --wine-glow: #8c1a22;
    --cream: #f6efe6;
    --flavour-red: #e0231c;
    --gold: #b57a3e;
    --gold-dark: #5a3515;
    --icon-gold: #c08a4a;
    --dash: #8a7a7a;
  }
  * { box-sizing: border-box; margin: 0; padding: 0; }
  html, body { width: 1200px; height: 1200px; overflow: hidden; }
  body {
    background: var(--backdrop);
    position: relative;
    font-family: "Crimson Text", Georgia, serif;
    color: var(--cream);
  }
  .package { position: absolute; left: 70px; top: 150px; width: 1060px; height: 900px; display: flex; }

  .front-panel {
    position: relative; width: 680px; height: 900px; overflow: hidden;
    background:
      radial-gradient(ellipse 70% 45% at 60% 18%, var(--wine-glow) 0%, var(--wine) 35%, transparent 75%),
      linear-gradient(170deg, var(--maroon) 0%, var(--maroon-deep) 60%, #240508 100%);
  }
  .brand-name {
    position: absolute; left: 110px; top: 110px;
    font-family: "Della Respira", Georgia, serif; font-size: 104px; letter-spacing: 1px;
    color: var(--cream); transform: rotate(5deg); transform-origin: left top;
  }
  .hero-photo { position: absolute; left: 40px; top: 300px; width: 400px; height: 600px; }
  .flavour-block { position: absolute; left: 360px; top: 550px; transform: rotate(7deg); transform-origin: left top; }
  .flavour-name {
    font-family: "Almendra", Georgia, serif; font-weight: 700; font-size: 66px;
    color: var(--flavour-red); line-height: 1;
  }
  .flavour-sub { font-size: 34px; letter-spacing: 1px; margin-top: 10px; margin-left: -14px; }
  .volume { position: absolute; right: 40px; bottom: 50px; text-align: right; transform: rotate(7deg); }
  .volume-num { font-family: "Crimson Text", Georgia, serif; font-weight: 700; font-size: 84px; line-height: .8; }
  .volume-unit { font-size: 34px; }
  .volume-abv { font-size: 24px; margin-top: 4px; }

  .side-panel {
    position: relative; width: 380px; height: 900px; padding: 70px 36px 0;
    background: linear-gradient(180deg, #2a0509 0%, var(--maroon-deep) 55%, #1e0c12 100%);
    border-left: 1px solid #12020400;
  }
  .side-brand { font-family: "Della Respira", Georgia, serif; font-size: 46px; text-align: center; }
  .side-flavour { font-family: "Almendra", Georgia, serif; font-size: 24px; color: #c23a2a; text-align: center; margin-top: 4px; }
  .side-rule { border: 0; border-top: 1px solid #6a3a2c; margin: 28px 0 14px; }
  .side-intro { font-size: 16px; line-height: 1.4; text-align: center; }
  .side-band {
    margin: 20px -36px 18px; height: 38px; line-height: 38px; text-align: center; font-size: 22px;
    background: linear-gradient(90deg, var(--gold-dark), var(--gold) 50%, var(--gold-dark));
  }
  .tip { display: flex; gap: 14px; align-items: flex-start; margin-bottom: 26px; }
  .tip--right { flex-direction: row-reverse; text-align: right; }
  .tip-title { color: var(--flavour-red); font-weight: 700; font-size: 16px; }
  .tip-text { font-size: 12px; line-height: 1.35; }
  .tip-icon { flex: 0 0 34px; }
  .tap-outline { position: absolute; left: 60px; top: 640px; }
  .side-abv { position: absolute; left: 0; right: 0; bottom: 40px; text-align: center; font-size: 18px; }
</style>
</head>
<body>
  <div class="package">
    <section class="front-panel">
      <div class="brand-name">Corvella</div>
      <div class="hero-photo" role="img" aria-label="Glass of red sangria with citrus slices, a lemon slice on the rim, halved lemon and mint leaves"
           style="background: radial-gradient(ellipse 45% 35% at 45% 35%, #5a0f1c 0%, #3a0810 70%, transparent 100%), radial-gradient(ellipse 45% 25% at 55% 85%, #c9a640 0%, #4d6a2a 55%, transparent 100%);"></div>
      <div class="flavour-block">
        <div class="flavour-name">Sangria</div>
        <div class="flavour-sub">Red Wine &amp; Citrus</div>
      </div>
      <div class="volume">
        <div><span class="volume-num">3</span><span class="volume-unit">ltr</span></div>
        <div class="volume-abv">10% alc.</div>
      </div>
    </section>

    <section class="side-panel">
      <div class="side-brand">Corvella</div>
      <div class="side-flavour">Sangria</div>
      <hr class="side-rule">
      <p class="side-intro">Crafted from ripe Spanish red wine blended with fresh orange and lemon, this sangria is smooth, bright and ready to pour for any gathering.</p>
      <div class="side-band">Red Wine &amp; Citrus</div>

      <div class="tip tip--right">
        <svg class="tip-icon" width="34" height="40" viewBox="0 0 34 40" fill="none" stroke="var(--icon-gold)" stroke-width="2">
          <path d="M3 4h28L17 20z"/><path d="M17 20v14M9 36h16"/><circle cx="26" cy="6" r="4"/>
        </svg>
        <div>
          <div class="tip-title">Serve Chilled</div>
          <div class="tip-text">Pour over ice with sliced fruit for a refreshing glass.</div>
        </div>
      </div>
      <div class="tip">
        <svg class="tip-icon" width="34" height="40" viewBox="0 0 34 40" fill="none" stroke="var(--icon-gold)" stroke-width="2">
          <path d="M4 6h20v8H14v8H8V10H4z"/><path d="M11 26v8"/>
        </svg>
        <div>
          <div class="tip-title">Easy Tap</div>
          <div class="tip-text">Press the tap gently and pour; stays fresh for weeks.</div>
        </div>
      </div>
      <div class="tip tip--right">
        <svg class="tip-icon" width="34" height="34" viewBox="0 0 34 34" fill="none" stroke="var(--icon-gold)" stroke-width="2">
          <circle cx="17" cy="17" r="14"/><circle cx="17" cy="17" r="9"/><path d="M17 8v18M8 17h18"/>
        </svg>
        <div>
          <div class="tip-title">Fresh Citrus</div>
          <div class="tip-text">Real orange and lemon notes balance the rich red wine.</div>
        </div>
      </div>

      <svg class="tap-outline" width="180" height="200" viewBox="0 0 180 200" fill="none" stroke="var(--dash)" stroke-width="2" stroke-dasharray="6 5">
        <path d="M4 30 Q70 4 176 4 V130 L150 160 V196 H60 V160 L4 130 Z"/>
        <path d="M60 160 Q60 140 90 135 H130 Q150 140 150 160"/>
      </svg>
      <div class="side-abv">10% alc./vol.</div>
    </section>
  </div>
</body>
</html>
```